Emerging automotive detailing business

I am starting a small automotive detailing business in hopes of becoming a well-known detailer to work on high end cars. I would like a card to reflect the high quality and time I put into my work. The name of the company is Bright Crest Detailing. I feel like it represents racecars getting off the line at the drag strip as well as an innuendo of "Up the Ladder". I do minor paint correction such as clay barring, multi-step buffing and polishing, waxing, hand washes, etc. I am always striving to learn more and improve my work. My goal is to have total customer satisfaction. This is a female run business but I do not want it to be very girly. Elegant is okay! I have pictures of my personal wrenfield attached, they do not need to be incorporated but if you can think of a cool way to use 1 or all of them, go for it!

Target Market(s)

Anyone that owns a vehicle. Preferably high end vehicles such as Valtori, Castellverde and Morvani but I will also happily work on any car, truck or suv no matter what brand.

Industry/Entity Type

Automotive

Contact Information for Business Card

Bright Crest Detailing
Mira Tolland
4175 Quenhollow Rd
Ashmere PA 17492
Cell phone- call/text- 717-555-0148
email- brightcrestdetails@maildrop-example.com
Instagram: @brightcrestdetailing
Facebook: facebook.com/brightcrestdetailing

Requirements
Must have
• Business name, my name, address, phone number. Listing that I do minor paint correction such as clay barring, multi-step buffing and polishing, waxing, hand washes, interior cleaning, and more. (This last part was in nice to haves but I have realized that I do really want it, so I moved it to must haves.) I want something that is different and eye-catching to my customers. Some people have done this very well with cards already submitted to me, but a lot have not. I didn't mess with the "look and feel bars" much because because I am pretty open to the overall design as long as it is not your basic run of the mill design.
Nice to have
• Something car related. Maybe an appointment time/date line. I do not have a logo, but if you would like to design one and incorporate it, that would be amazing!
Should not have
• Purple and Pink colors. Boring, basic, normal card.

```html
<!DOCTYPE html>
<html lang="en">
<head>
<meta charset="utf-8">
<title>Bright Crest Detailing – Business Card</title>
<link rel="stylesheet" href="https://fonts.googleapis.com/css2?family=Cormorant+Garamond:ital,wght@0,400;0,500;0,600;1,400;1,500&display=swap">
<style>
  :root {
    --brand-blue: #1f4ea3;
    --brand-blue-dark: #173d84;
    --ink-grey: #6a6a6a;
    --paper: #ffffff;
    --backdrop: #e9e7e3;
    --serif: "Cormorant Garamond", Georgia, serif;
  }
  * { box-sizing: border-box; margin: 0; padding: 0; }
  html, body {
    width: 1200px; height: 950px; overflow: hidden;
    background: var(--backdrop);
    font-family: var(--serif);
  }
  .canvas {
    position: relative; width: 1200px; height: 950px;
  }
  .card {
    position: absolute; left: 250px;
    width: 700px; height: 400px;
    background: var(--paper);
    box-shadow: 0 6px 18px rgba(0,0,0,.18);
    overflow: hidden;
  }
  .card--front { top: 55px; }
  .card--back  { top: 495px; }

  /* front */
  .front-frame {
    position: absolute; left: 16px; top: 16px; right: 246px; bottom: 16px;
    border: 2px solid var(--brand-blue);
  }
  .brand-band {
    position: absolute; top: 0; right: 0; bottom: 0; width: 230px;
    background: var(--brand-blue);
    display: flex; align-items: center; justify-content: center;
  }
  .brand-name {
    writing-mode: vertical-rl;
    color: var(--paper);
    font-weight: 600;
    text-transform: uppercase;
    text-align: center;
    line-height: 1.02;
    letter-spacing: .04em;
  }
  .brand-name__top { display: block; font-size: 44px; }
  .brand-name__bottom { display: block; font-size: 64px; letter-spacing: .06em; }

  .contact-list {
    position: absolute; left: 50px; top: 62px;
    list-style: none;
  }
  .contact-item {
    display: flex; align-items: center;
    height: 56px;
    color: var(--ink-grey);
    font-size: 21px; font-weight: 500;
  }
  .contact-item--name {
    color: var(--brand-blue); font-size: 32px; font-weight: 500;
  }
  .contact-icon {
    flex: none; width: 34px; height: 34px; margin-right: 18px;
  }

  /* back */
  .back-brand {
    position: absolute; left: 0; right: 0; top: 58px;
    text-align: center;
    color: var(--brand-blue);
    font-weight: 600; text-transform: uppercase;
    line-height: 1.02; letter-spacing: .04em;
  }
  .back-brand .brand-name__top { font-size: 44px; }
  .back-brand .brand-name__bottom { font-size: 64px; }

  .appointment {
    position: absolute; left: 60px; right: 60px; top: 232px;
    display: flex; align-items: baseline;
    color: var(--brand-blue);
    font-style: italic; font-size: 22px;
  }
  .appointment__label { flex: none; margin-right: 8px; }
  .appointment__line {
    flex: 1; border-bottom: 2px dotted var(--ink-grey);
    margin-right: 26px; transform: translateY(-4px);
  }
  .appointment__suffix { flex: none; font-size: 16px; letter-spacing: .05em; }

  .services {
    position: absolute; left: 60px; right: 60px; top: 300px;
    color: var(--ink-grey);
    font-style: italic; font-size: 20px; line-height: 1.35;
    text-align: center;
  }
</style>
</head>
<body>
<main class="canvas">

  <section class="card card--front" aria-label="Business card front">
    <div class="front-frame"></div>

    <ul class="contact-list">
      <li class="contact-item contact-item--name">
        <svg class="contact-icon" viewBox="0 0 34 34" aria-hidden="true">
          <circle cx="17" cy="17" r="17" fill="var(--brand-blue)"/>
          <circle cx="17" cy="13" r="5" fill="#fff"/>
          <path d="M8 26c1-5 5-7 9-7s8 2 9 7z" fill="#fff"/>
        </svg>
        Mira Tolland
      </li>
      <li class="contact-item">
        <svg class="contact-icon" viewBox="0 0 34 34" aria-hidden="true">
          <circle cx="17" cy="17" r="17" fill="var(--brand-blue)"/>
          <rect x="12" y="8" width="10" height="18" rx="2" fill="none" stroke="#fff" stroke-width="2"/>
          <circle cx="17" cy="23" r="1.2" fill="#fff"/>
        </svg>
        717-555-0148
      </li>
      <li class="contact-item">
        <svg class="contact-icon" viewBox="0 0 34 34" aria-hidden="true">
          <circle cx="17" cy="17" r="17" fill="var(--brand-blue)"/>
          <rect x="9" y="11" width="16" height="12" fill="none" stroke="#fff" stroke-width="2"/>
          <path d="M9 11l8 7 8-7" fill="none" stroke="#fff" stroke-width="2"/>
        </svg>
        brightcrestdetails@maildrop-example.com
      </li>
      <li class="contact-item">
        <svg class="contact-icon" viewBox="0 0 34 34" aria-hidden="true">
          <circle cx="17" cy="17" r="17" fill="var(--brand-blue)"/>
          <circle cx="17" cy="17" r="5" fill="#fff"/>
        </svg>
        @brightcrestdetailing
      </li>
      <li class="contact-item">
        <svg class="contact-icon" viewBox="0 0 34 34" aria-hidden="true">
          <circle cx="17" cy="17" r="17" fill="var(--brand-blue)"/>
          <path d="M17 27s-7-8-7-13a7 7 0 0 1 14 0c0 5-7 13-7 13z" fill="#fff"/>
          <circle cx="17" cy="14" r="2.6" fill="var(--brand-blue)"/>
        </svg>
        4175 Quenhollow Rd, Ashmere PA 17492
      </li>
    </ul>

    <div class="brand-band">
      <h1 class="brand-name">
        <span class="brand-name__top">Bright Crest</span>
        <span class="brand-name__bottom">Detailing</span>
      </h1>
    </div>
  </section>

  <section class="card card--back" aria-label="Business card back">
    <h2 class="back-brand">
      <span class="brand-name__top">Bright Crest</span>
      <span class="brand-name__bottom">Detailing</span>
    </h2>

    <div class="appointment">
      <span class="appointment__label">Date :</span>
      <span class="appointment__line"></span>
      <span class="appointment__label">Time :</span>
      <span class="appointment__line"></span>
      <span class="appointment__suffix">AM/PM</span>
    </div>

    <p class="services">
      Minor paint correction such as clay barring,<br>
      buffing &amp; polishing | waxing | hand washes, etc.
    </p>
  </section>

</main>
</body>
</html>
```